Company identity deisgn should support 2 languages

I would like to get our company identity design
This includes the following only
Business Cards 2 languages Arabic and English
Email signature
Letterhead
Linkedin profile images
Attached is the logo in Ai format

Requirements
Must have
• For business card
Must have
Name and Adrees in arabic
Name and Address in english
You might use both side of the card
Should not have
• Any pictures other than the logo

```html
<!DOCTYPE html>
<html lang="en">
<head>
<meta charset="utf-8">
<title>Northwind Cognitive – Business Cards</title>
<link rel="stylesheet" href="https://fonts.googleapis.com/css2?family=Mulish:wght@400;500;600&family=Cairo:wght@400;600;700&display=swap">
<style>
  :root {
    --bg: #8c8c8c;
    --card: #ffffff;
    --brand-blue: #1474bf;
    --ink: #3d3d3d;
    --muted: #8a8a8a;
    --rule: #9a9a9a;
  }
  * { box-sizing: border-box; margin: 0; padding: 0; }
  html, body { width: 1200px; height: 1200px; overflow: hidden; }
  body {
    background: var(--bg);
    font-family: "Mulish", sans-serif;
    color: var(--ink);
    position: relative;
  }
  .card {
    position: absolute;
    left: 257px;
    width: 686px;
    height: 392px;
    background: var(--card);
    border-radius: 26px;
    overflow: hidden;
  }
  .card--english { top: 165px; }
  .card--arabic { top: 653px; }

  .brand {
    position: absolute;
    right: 38px;
    top: 52px;
    display: flex;
    align-items: center;
    gap: 12px;
  }
  .brand__dot {
    width: 34px; height: 34px;
    border-radius: 50%;
    background: var(--brand-blue);
  }
  .brand__name {
    font-family: "Mulish", sans-serif;
    font-weight: 600;
    font-size: 20px;
    letter-spacing: 0.5px;
    color: var(--brand-blue);
    text-transform: uppercase;
  }

  .person { position: absolute; left: 39px; top: 240px; }
  .person__name {
    font-size: 22px;
    font-weight: 600;
    color: var(--brand-blue);
    letter-spacing: 0.3px;
    line-height: 1.1;
  }
  .person__title {
    font-size: 15px;
    color: var(--muted);
    margin-top: 6px;
  }
  .card--arabic .person { left: 36px; top: 232px; }
  .card--arabic .person__name,
  .card--arabic .person__title { font-family: "Cairo", sans-serif; }
  .card--arabic .person__name { font-size: 24px; font-weight: 700; }
  .card--arabic .person__title { font-size: 17px; margin-top: 0; line-height: 1; }

  .rule {
    position: absolute;
    left: 39px; right: 42px;
    top: 297px;
    height: 1px;
    background: var(--rule);
  }
  .card--arabic .rule { left: 36px; top: 298px; background: #c4c4c4; }

  .contact {
    position: absolute;
    top: 318px;
    font-size: 14.5px;
    line-height: 19px;
    color: var(--ink);
  }
  .contact--address { left: 41px; }
  .contact--phone { left: 272px; top: 321px; }
  .contact--web { left: 435px; }
  .card--arabic .contact--address { left: 37px; top: 319px; font-family: "Cairo", sans-serif; font-size: 15px; line-height: 22px; }
  .card--arabic .contact--phone { left: 234px; top: 328px; font-size: 16.5px; line-height: 20px; }
  .card--arabic .contact--web { left: 413px; top: 324px; font-size: 17px; line-height: 19px; }

  .band {
    position: absolute;
    left: 0; right: 0; bottom: 0;
    height: 12px;
    background: var(--brand-blue);
  }
  .band__dot {
    position: absolute;
    top: 3px;
    width: 6px; height: 6px;
    border-radius: 50%;
    background: var(--card);
  }
  .band__dot--left { left: 36px; }
  .band__dot--right { right: 34px; }
</style>
</head>
<body>

<section class="card card--english" lang="en">
  <div class="brand">
    <span class="brand__dot"></span>
    <span class="brand__name">Northwind Cognitive</span>
  </div>
  <div class="person">
    <h1 class="person__name">DANIEL HAYES</h1>
    <p class="person__title">President</p>
  </div>
  <div class="rule"></div>
  <address class="contact contact--address" style="font-style:normal">4210 Cedar Ridge Road<br>Juneau, Alaska 99801</address>
  <p class="contact contact--phone">P. 555-014-2870<br>C. 555-016-9314</p>
  <p class="contact contact--web">info@northwindcognitive.com<br>www.northwindcognitive.com</p>
  <div class="band"><span class="band__dot band__dot--left"></span><span class="band__dot band__dot--right"></span></div>
</section>

<section class="card card--arabic">
  <div class="brand">
    <span class="brand__dot"></span>
    <span class="brand__name">Northwind Cognitive</span>
  </div>
  <div class="person" lang="ar" dir="rtl">
    <h1 class="person__name">دانيال هايز</h1>
    <p class="person__title">رئيس</p>
  </div>
  <div class="rule"></div>
  <address class="contact contact--address" lang="ar" style="font-style:normal">4210 طريق سيدار ريدج<br>جونو، ألاسكا 99801</address>
  <p class="contact contact--phone">P. 555-014-2870<br>C. 555-016-9314</p>
  <p class="contact contact--web">info@northwindcognitive.com<br>www.northwindcognitive.com</p>
  <div class="band"><span class="band__dot band__dot--left"></span><span class="band__dot band__dot--right"></span></div>
</section>

</body>
</html>
```